Business Card - high end, modern health care

Hey designers!

We need a double sided business card for the boutique, cutting edge physical therapy rehabilitation centre in Sydney's Northern Beaches.

With the most qualified physios in the area The Harbourview Motion Clinic does what other physiotherapy practices do not, we take our time with our patients giving them longer appointments, better physios and therefor faster results!

We guarantee that the service people receive at THMC will be unparalleled.

Hence we need a business card to reflect our modern, boutique, high end service. The final design needs to reflect that we are in a class of our own yet with the feel of beachside retreat.

Below I have attached our logo in both blue on white and white on blue. The exact colour is;
and the font that we have used in our logo is Tex Gyre Aventador.

I like the idea of the blue as the main colour as it is more eye catching and our signage onto the main road will be in this blue and in the interest of consistency across marketing the blue needs to be a part of the design. However I would appreciate a few designs onto a wooden background as this is a visual theme within the fitout of the practice.

The design needs to be of standard size (91x55mm).

Target Market(s)

We target people who have an end outcome in mind and those who have had poor experiences with other providers and ensure that everyone gets the care that they deserve with a premium service that is tailored to the individuals circumstances. As a premium service, the target market is highly educated, business and tech savvy with the additional target market of elderly people who have self funded their retirement and see value in paying for the best ongoing rehabilitation to maintain independence.

Industry/Entity Type

Physical Therapy

Contact Information for Business Card

Name, designation( Titled Musculoskeletal Physiotherapist... there will also be those in the company that have multiple designations ie 5 or 6 words long), phone number, email, facebook, instagram, address

Font styles to use
Sans Serif

Colors

Designer to choose colors to be used in the design.

Requirements
Must have
• Front - The logo as large as possible, blue or wooden theme, and all of the important details.
• Back - A blank space/lines on which to write appointment times (no "Appointment, date, time" etc.)
Nice to have
• facebook url
• logos for facebook and instagram
• Mini logos for the phone and email?

```html
<!DOCTYPE html>
<html lang="en">
<head>
<meta charset="utf-8">
<title>The Harbourview Motion Clinic – Business Card</title>
<link rel="stylesheet" href="https://fonts.googleapis.com/css2?family=Roboto:wght@400;500&family=Roboto+Condensed:wght@500;700&family=Open+Sans:wght@400&display=swap">
<style>
  :root {
    --brand-blue: #0b57a8;
    --ink-grey: #555b61;
    --label-grey: #5d6166;
    --rule-grey: #6b6f74;
    --card-white: #f6f6f6;
    --back-white: #ffffff;
    --watermark: #eef2f8;
    --backdrop: #2a2a2a;
  }
  * { box-sizing: border-box; margin: 0; padding: 0; }
  html, body { width: 1200px; height: 960px; overflow: hidden; }
  body { background: var(--backdrop); position: relative; font-family: "Roboto", Arial, sans-serif; }

  .card { position: absolute; width: 598px; height: 342px; border-radius: 18px; overflow: hidden; }
  .card--front { left: 322px; top: 108px; background: var(--card-white); }
  .card--back { left: 320px; top: 493px; width: 600px; background: var(--back-white); }

  .brand-panel { position: absolute; left: 0; top: 0; }
  .brand-panel__mark {
    position: absolute; left: 105px; top: 147px; width: 170px; text-align: center;
    font-family: "Roboto Condensed", "Arial Narrow", sans-serif; font-weight: 700;
    font-size: 40px; letter-spacing: 3px; color: #fff;
  }

  .details { position: absolute; right: 21px; top: 0; text-align: right; }
  .clinic-name {
    position: absolute; right: 0; top: 40px; white-space: nowrap;
    font-family: "Roboto Condensed", "Arial Narrow", sans-serif; font-weight: 700;
    color: var(--brand-blue); text-transform: uppercase; line-height: 1;
  }
  .clinic-name__main { display: block; font-size: 27px; }
  .clinic-name__sub { display: block; font-size: 15px; font-weight: 500; letter-spacing: 5.6px; margin-top: 4px; margin-right: -5px; }

  .person { position: absolute; right: 0; top: 106px; white-space: nowrap; }
  .person__name { font-family: "Roboto Condensed", "Arial Narrow", sans-serif; font-weight: 700; font-size: 22px; color: var(--brand-blue); line-height: 1; }
  .person__role { font-family: "Roboto Condensed", "Arial Narrow", sans-serif; font-weight: 500; font-size: 15px; color: var(--ink-grey); margin-top: 5px; }

  .contact-list { position: absolute; right: 0; top: 160px; list-style: none; }
  .contact-list li { display: flex; justify-content: flex-end; align-items: center; height: 19px; font-size: 14.5px; color: var(--ink-grey); white-space: nowrap; }
  .contact-list .icon { width: 13px; height: 13px; margin-left: 9px; flex: none; }
  .address { position: absolute; right: 0; top: 264px; display: flex; align-items: flex-start; font-size: 14.5px; color: var(--ink-grey); line-height: 19px; white-space: nowrap; }
  .address .icon { width: 12px; height: 16px; margin-left: 10px; margin-top: 2px; }

  .watermark { position: absolute; left: 150px; top: 29px; }
  .watermark__name {
    position: absolute; left: 150px; top: 150px; width: 300px; text-align: center;
    font-family: "Roboto Condensed", "Arial Narrow", sans-serif; font-weight: 700;
    font-size: 52px; letter-spacing: 4px; color: var(--watermark);
  }
  .field-label { position: absolute; font-family: "Open Sans", Arial, sans-serif; font-size: 16px; color: var(--label-grey); line-height: 1; }
  .write-line { position: absolute; height: 1px; background: var(--rule-grey); }
</style>
</head>
<body>

<section class="card card--front" aria-label="Business card front">
  <svg class="brand-panel" width="598" height="342" viewBox="0 0 598 342" aria-hidden="true">
    <path fill="var(--brand-blue)" d="M0 0 H185 A171 171 0 0 1 185 342 H0 Z"/>
  </svg>
  <div class="brand-panel__mark">THMC</div>

  <div class="details">
    <h1 class="clinic-name">
      <span class="clinic-name__main">The Harbourview</span>
      <span class="clinic-name__sub">Motion Clinic</span>
    </h1>

    <div class="person">
      <div class="person__name">LIAM CARTER</div>
      <div class="person__role">CEO/FOUNDER</div>
    </div>

    <ul class="contact-list">
      <li>612 555 0148
        <svg class="icon" viewBox="0 0 16 16" aria-hidden="true"><path fill="var(--brand-blue)" d="M3.6 1 6 3.6 4.7 5.4c.8 2.2 3.3 4.9 5.9 5.9l1.8-1.3L15 12.4 13 15C6.5 14.4 1.6 9.5 1 3z"/></svg>
      </li>
      <li>liam@harbourview.com
        <svg class="icon" viewBox="0 0 16 16" aria-hidden="true"><rect x="1" y="3" width="14" height="10" fill="var(--brand-blue)"/><path d="M1.5 3.6 8 9l6.5-5.4" fill="none" stroke="#fff" stroke-width="1.3"/></svg>
      </li>
      <li>www.harbourview.com
        <svg class="icon" viewBox="0 0 16 16" aria-hidden="true"><circle cx="8" cy="8" r="6.3" fill="none" stroke="var(--brand-blue)" stroke-width="1.6"/><ellipse cx="8" cy="8" rx="2.6" ry="6.3" fill="none" stroke="var(--brand-blue)" stroke-width="1.3"/><path d="M1.8 8h12.4" stroke="var(--brand-blue)" stroke-width="1.3"/></svg>
      </li>
      <li>/harbourviewclinic
        <svg class="icon" viewBox="0 0 16 16" aria-hidden="true"><rect x="1.5" y="1.5" width="13" height="13" fill="var(--brand-blue)"/></svg>
      </li>
      <li>@harbourview
        <svg class="icon" viewBox="0 0 16 16" aria-hidden="true"><rect x="1.5" y="1.5" width="13" height="13" fill="var(--brand-blue)"/></svg>
      </li>
    </ul>

    <div class="address">
      <div>14 Seaview Parade<br>Manly, NSW 2095</div>
      <svg class="icon" viewBox="0 0 12 16" aria-hidden="true"><path fill="var(--brand-blue)" d="M6 0a6 6 0 0 1 6 6c0 4-6 10-6 10S0 10 0 6a6 6 0 0 1 6-6z"/><circle cx="6" cy="6" r="2.2" fill="#fff"/></svg>
    </div>
  </div>
</section>

<section class="card card--back" aria-label="Business card back">
  <svg class="watermark" width="300" height="300" viewBox="0 0 300 300" aria-hidden="true">
    <circle cx="150" cy="148" r="140" fill="none" stroke="var(--watermark)" stroke-width="14"/>
  </svg>
  <div class="watermark__name" aria-hidden="true">THMC</div>

  <span class="field-label" style="left:32px; top:43px;">Name</span>
  <div class="write-line" style="left:80px; width:478px; top:56px;"></div>

  <span class="field-label" style="left:32px; top:86px;">Date</span>
  <div class="write-line" style="left:72px; width:261px; top:98px;"></div>
  <span class="field-label" style="left:340px; top:86px;">Time</span>
  <div class="write-line" style="left:383px; width:114px; top:98px;"></div>
  <span class="field-label" style="left:503px; top:86px;">am/pm</span>

  <div class="write-line" style="left:35px; width:523px; top:139px;"></div>
  <div class="write-line" style="left:35px; width:523px; top:179px;"></div>
  <div class="write-line" style="left:35px; width:523px; top:219px;"></div>
  <div class="write-line" style="left:35px; width:523px; top:259px;"></div>
  <div class="write-line" style="left:35px; width:523px; top:299px;"></div>
</section>

</body>
</html>
```